Food and Beverage Business Cards

We need business cards with logo designs for a consultant in the food and beverage industry. We specialize in helping restaurants fix operational and management problems.
Specific areas of expertise include:
-Steps of service
-Staff management tools
-Standard operating procedures
-Profit and loss management
-Inventory
-Point of sales
-Bar Menu
-Mystery shopper service
-Handling and managing suppliers

Target Market(s)

Restaurant and bar owners and managers

Industry/Entity Type

Business

Contact Information for Business Card

Mathieu Girardot
Q&T Consulting
phone: 15027390614
mathqt@sampleinbox.com

Font styles to use
Other font styles liked:
• Check out the screen shot font idea

Colors

Designer to choose colors to be used in the design.

Requirements
Must have
• Must include QR code (See attachment)
• Logo should reflect our specific focus on the drinks side of the industry.
• Areas of Expertise:
• -Service Steps
• -Staff management tools
• -S.O.P
• -P&L Management
• -Inventory
• -P.O.S
• -Bar Menu
• -Mystery Shopper Service
• -Handling and Managing Suppliers

```html
<!DOCTYPE html>
<html lang="en">
<head>
<meta charset="utf-8">
<title>Q&amp;T Consulting Business Cards</title>
<link rel="stylesheet" href="https://fonts.googleapis.com/css2?family=Open+Sans:wght@400;700&display=swap">
<style>
  :root {
    --backdrop: #3b3330;
    --card: #141414;
    --card-edge: #222222;
    --white: #f4f4f4;
    --grey-text: #9a9a9a;
    --grey-mark: #6e6e6e;
    --badge-green: #2f5a32;
    --badge-dark: #2a2a2a;
    --badge-light: #d8d8d8;
  }
  html, body {
    margin: 0;
    padding: 0;
    width: 1200px;
    height: 864px;
    overflow: hidden;
    background: var(--backdrop);
    font-family: "Open Sans", Arial, sans-serif;
  }
  .canvas {
    position: relative;
    width: 1200px;
    height: 864px;
  }
  .card {
    position: absolute;
    width: 540px;
    height: 310px;
    background: var(--card);
    border: 1px solid var(--card-edge);
    box-shadow: 0 18px 40px rgba(0,0,0,0.45);
    box-sizing: border-box;
  }
  /* Expertise side */
  .card--expertise { left: 40px; top: 150px; }
  .expertise__mark {
    position: absolute;
    left: 120px;
    top: 34px;
    font-size: 86px;
    font-weight: 400;
    color: var(--grey-mark);
    letter-spacing: 2px;
    line-height: 1;
  }
  .expertise__badges {
    position: absolute;
    right: 30px;
    top: 30px;
    display: flex;
    gap: 8px;
  }
  .badge {
    width: 42px;
    height: 42px;
    border-radius: 50%;
  }
  .badge--green { background: var(--badge-green); }
  .badge--dark { background: var(--badge-dark); border: 2px solid var(--badge-light); box-sizing: border-box; }
  .badge--light { background: var(--badge-light); }
  .expertise__title {
    position: absolute;
    left: 0;
    right: 0;
    top: 158px;
    text-align: center;
    font-size: 19px;
    font-weight: 700;
    color: var(--grey-text);
  }
  .expertise__list {
    position: absolute;
    left: 20px;
    right: 20px;
    top: 192px;
    text-align: center;
    font-size: 14px;
    line-height: 1.45;
    color: var(--grey-text);
  }
  /* Contact side */
  .card--contact { left: 620px; top: 410px; }
  .contact__mark {
    position: absolute;
    left: 0;
    right: 0;
    top: 54px;
    text-align: center;
    color: var(--white);
    font-weight: 700;
    line-height: 1;
  }
  .contact__mark-name { display: block; font-size: 78px; }
  .contact__mark-place { display: block; font-size: 22px; letter-spacing: 6px; margin-top: 4px; }
  .contact__person {
    position: absolute;
    right: 290px;
    top: 204px;
    text-align: right;
    color: var(--white);
  }
  .contact__name { font-size: 18px; font-weight: 700; margin: 0; }
  .contact__role { font-size: 14px; margin: 2px 0 0; }
  .contact__divider {
    position: absolute;
    left: 268px;
    top: 200px;
    width: 1px;
    height: 66px;
    background: var(--white);
  }
  .contact__details {
    position: absolute;
    left: 288px;
    top: 214px;
    margin: 0;
    padding: 0;
    list-style: none;
    color: var(--white);
    font-size: 15px;
  }
  .contact__details li {
    display: flex;
    align-items: center;
    gap: 8px;
    margin-bottom: 6px;
  }
  .contact__details svg { width: 13px; height: 13px; fill: var(--white); }
</style>
</head>
<body>
<main class="canvas">

  <section class="card card--expertise">
    <div class="expertise__mark">Q&amp;T</div>
    <div class="expertise__badges">
      <span class="badge badge--green"></span>
      <span class="badge badge--dark"></span>
      <span class="badge badge--light"></span>
    </div>
    <h2 class="expertise__title">Areas of Expertise</h2>
    <p class="expertise__list">
      Service Steps | Staff management tools | S.O.P | P&amp;L Management<br>
      Inventory | P.O.S | Bar Menu | Mystery Shopper Service<br>
      Handling and Managing Suppliers
    </p>
  </section>

  <section class="card card--contact">
    <div class="contact__mark">
      <span class="contact__mark-name">Q&amp;T</span>
      <span class="contact__mark-place">harbor</span>
    </div>
    <div class="contact__person">
      <p class="contact__name">Mathieu Girardot</p>
      <p class="contact__role">Q&amp;T Consulting</p>
    </div>
    <span class="contact__divider"></span>
    <ul class="contact__details">
      <li>
        <svg viewBox="0 0 16 16" aria-hidden="true"><path d="M2 5c0-2 3-3 6-3s6 1 6 3v1h-3V4.5H5V6H2z M3 7h10l1 7H2z M8 9a2 2 0 1 0 0 4a2 2 0 1 0 0-4z"/></svg>
        15027390614
      </li>
      <li>
        <svg viewBox="0 0 16 16" aria-hidden="true"><path d="M1 3h14v2L8 9 1 5z M1 7l7 4 7-4v6H1z"/></svg>
        mathqt@sampleinbox.com
      </li>
    </ul>
  </section>

</main>
</body>
</html>
```